Letterhead and matching envelope design for a dental office

We need a new stationary design, letterhead and envelope #10, for a dental office in Denver area. We are called Bright Harbor Dental. We want a simple and minimalistic design but not a boring design. I wish to have one good point that makes it look professional. I have attached our logo. Feel free to use either one. I want the design for letterhead and envelope look like a "matching pair" but not look the same. The envelope doesn't have to be white and it will have an address window on bottom left.

Target Market(s)

everyone who visits dentist (adults)

Industry/Entity Type

Dental

Font styles to use
Other font styles liked:
• close to font on logo or something that matches well

Requirements
Must have
• professional
• simple, minimalistic
• unique point that stands out
Nice to have
• matching but not same design for letterhead and envelope
Should not have
• not look like all the other boring designs
• no flowery, distracting feats

```html
<!DOCTYPE html>
<html lang="en">
<head>
<meta charset="utf-8">
<title>Bright Harbor Dental — Stationery</title>
<link href="https://fonts.googleapis.com/css2?family=Cinzel:wght@700&family=Montserrat:wght@400;500&family=Cormorant+Garamond:wght@500&display=swap" rel="stylesheet">
<style>
  :root {
    --brand-green: #44b649;
    --paper: #ffffff;
    --backdrop: #d3d4d6;
  }
  * { margin: 0; padding: 0; box-sizing: border-box; }
  html, body { width: 1200px; height: 927px; overflow: hidden; background: var(--backdrop); }
  .canvas { position: relative; width: 1200px; height: 927px; }

  .sheet { position: absolute; overflow: hidden; }
  .sheet svg.shape { position: absolute; left: 0; top: 0; }

  .brand-name {
    font-family: "Cinzel", serif;
    font-weight: 700;
    color: var(--brand-green);
    letter-spacing: 1.2px;
    white-space: nowrap;
  }
  .brand-place {
    font-family: "Cormorant Garamond", serif;
    font-weight: 500;
    color: var(--brand-green);
    letter-spacing: 7px;
    white-space: nowrap;
  }
  .contact {
    font-family: "Montserrat", sans-serif;
    color: var(--brand-green);
    white-space: nowrap;
  }

  /* Letterhead */
  .letterhead { left: 169px; top: 65px; width: 417px; height: 539px; background: var(--paper); }
  .letterhead .brand-block { position: absolute; right: 21px; top: 80px; text-align: center; }
  .letterhead .brand-name { font-size: 14.5px; }
  .letterhead .brand-place { font-size: 8px; margin-top: 0; }
  .letterhead .contact-block { position: absolute; right: 21px; top: 473px; text-align: right; font-size: 9.5px; line-height: 11.5px; }
  .letterhead .contact-gap { height: 6px; }
  .letterhead .contact-line { display: flex; justify-content: flex-end; align-items: center; gap: 5px; }
  .letterhead .contact-line svg { width: 7px; height: 7px; }

  /* Folder */
  .folder { left: 619px; top: 65px; width: 417px; height: 539px; background: var(--brand-green); }
  .folder .seal { position: absolute; left: 209px; top: 271px; transform: translate(-50%, -50%); width: 250px; height: 250px; border: 1.5px solid var(--paper); border-radius: 50%; display: flex; flex-direction: column; align-items: center; justify-content: center; }
  .folder .brand-name, .envelope-back .brand-name { color: var(--paper); text-align: center; }
  .folder .brand-name { font-size: 26px; letter-spacing: 4px; line-height: 36px; }
  .folder .address { position: absolute; left: 0; width: 417px; top: 504px; text-align: center; font-size: 9.5px; color: var(--paper); }

  /* Envelope front */
  .envelope-front { left: 134px; top: 634px; width: 454px; height: 228px; background: var(--paper); }
  .envelope-front .flap { position: absolute; left: 0; top: 0; width: 454px; height: 22px; background: var(--brand-green); border-radius: 11px 11px 0 0; }
  .envelope-front .brand-block { position: absolute; left: 226px; top: 131px; transform: translateX(-50%); text-align: center; }
  .envelope-front .brand-name { font-size: 14.5px; }
  .envelope-front .brand-place { font-size: 8px; }
  .envelope-front .address { position: absolute; right: 16px; top: 204px; font-size: 12px; color: var(--paper); letter-spacing: .3px; }

  /* Envelope back */
  .envelope-back { left: 612px; top: 658px; width: 454px; height: 204px; background: var(--brand-green); }
  .envelope-back .flap { position: absolute; left: 0; top: 0; width: 454px; height: 22px; background: var(--paper); border-radius: 0 0 11px 11px; }
  .envelope-back .seal { position: absolute; left: 222px; top: 110px; transform: translate(-50%, -50%); width: 128px; height: 128px; border: 1.2px solid var(--paper); border-radius: 50%; display: flex; align-items: center; justify-content: center; }
  .envelope-back .brand-name { font-size: 13px; letter-spacing: 2px; line-height: 18px; }
</style>
</head>
<body>
<main class="canvas">

  <section class="sheet letterhead" aria-label="Letterhead">
    <svg class="shape" width="417" height="539" viewBox="0 0 417 539">
      <path d="M0 0 H31 C10 120 14 200 36 300 C56 390 52 460 33 539 H0 Z" fill="var(--brand-green)"/>
      <path d="M25 0 C4 120 8 200 30 300 C50 390 46 460 27 539" fill="none" stroke="var(--paper)" stroke-width="1.6"/>
    </svg>
    <div class="brand-block">
      <div class="brand-name">Bright Harbor Dental</div>
      <div class="brand-place">Riverside</div>
    </div>
    <div class="contact contact-block">
      <div>PO BOX 4821</div>
      <div>Elmwood SA 5190</div>
      <div class="contact-gap"></div>
      <div class="contact-line">+330 5182-9034
        <svg viewBox="0 0 10 10"><path d="M2 1 L4 1 L4.6 3.2 L3.4 4 C4 5.4 4.8 6.2 6 6.8 L6.8 5.6 L9 6.2 L9 8.2 C5 8.6 1.4 5 2 1 Z" fill="var(--brand-green)"/></svg>
      </div>
      <div class="contact-line">info@<b style="font-weight:500">brightharbor</b>.com
        <svg viewBox="0 0 10 10"><rect x="1" y="2" width="8" height="6" fill="none" stroke="var(--brand-green)" stroke-width="1.2"/><path d="M1 2 L5 5.4 L9 2" fill="none" stroke="var(--brand-green)" stroke-width="1.2"/></svg>
      </div>
    </div>
  </section>

  <section class="sheet folder" aria-label="Presentation folder">
    <svg class="shape" width="417" height="539" viewBox="0 0 417 539">
      <path d="M381 0 C405 120 412 200 388 300 C362 400 364 460 385 539 H417 V0 Z" fill="var(--paper)"/>
      <path d="M388 0 C412 120 419 200 395 300 C369 400 371 460 392 539" fill="none" stroke="var(--brand-green)" stroke-width="1.6"/>
    </svg>
    <div class="seal">
      <div class="brand-name">Bright<br>Harbor<br>Dental</div>
    </div>
    <div class="contact address">PO BOX 4821 Elmwood SA 5190</div>
  </section>

  <section class="sheet envelope-front" aria-label="Envelope front">
    <div class="flap"></div>
    <svg class="shape" width="454" height="228" viewBox="0 0 454 228">
      <path d="M0 194 C80 212 160 218 260 198 C340 182 410 180 454 196 V228 H0 Z" fill="var(--brand-green)"/>
      <path d="M0 200 C80 218 160 224 260 204 C340 188 410 186 454 202" fill="none" stroke="var(--paper)" stroke-width="1.4"/>
    </svg>
    <div class="brand-block">
      <div class="brand-name">Bright Harbor Dental</div>
      <div class="brand-place">Riverside</div>
    </div>
    <div class="contact address">PO BOX 4821 Elmwood SA 5190</div>
  </section>

  <section class="sheet envelope-back" aria-label="Envelope back">
    <div class="flap"></div>
    <div class="seal">
      <div class="brand-name">Bright<br>Harbor<br>Dental</div>
    </div>
  </section>

</main>
</body>
</html>
```